Dental Practice Billboard Design

We are a newer dental practice in need of a simple but appealing billboard for our growing dental practice to attract new patients. The practice is owned by husband and wife dentists and is family friendly in a small town in Kentucky. We try to be very friendly and caring to our patients. Would prefer a blue background for the billboard and our tooth logo to be prominent. We are partial to the Patua One font used in the image below but please feel free to tweak it as you deem necessary. The shape of the uppercase D and lowercase g are why we like that font, so fonts with a similarly shaped “D” and “g” would work as well. Please include our phone number (555) 847-1390. Please see our website Harlowbrookdentistry.example for more info on the practice if needed. Thank you! Looking forward to seeing your creation.
Updates

The dimensions will be 12ft x 24ft (3.6576m x 7.3152m). Apologies for not including this in the original prompt. Thank you all for your submissions.

Industry/Entity Type

Dental

Font styles to use
Other font styles liked:
• Patua One

Colors
0054AA
0677BA
7BADD7
CADEEF
E8F1F8
0094D4
00A9DD
6FCCEA
C7EBF8
E9F6FB
00AB8E
00BBA5
67D7C9
C6EFE9
E9F9F6
59FF00
82FF00
B8FF75
E3FFCB
F4FFEA

Requirements
Must have
• Phone number, website, Logo, Practice name “Harlow Brook Dentistry”
Should not have
• A tagline or slogan

```html
<!DOCTYPE html>
<html lang="en">
<head>
<meta charset="UTF-8">
<title>Harlow Brook Dentistry Billboard</title>
<link rel="stylesheet" href="https://fonts.googleapis.com/css2?family=Patua+One&family=Bree+Serif&display=swap">
<style>
  :root {
    --board-blue: #243d86;
    --brand-green: #6bb83f;
    --text-white: #ffffff;
    --page-bg: #eef2f7;
  }
  * { margin: 0; padding: 0; box-sizing: border-box; }
  html, body {
    width: 1200px;
    height: 1000px;
    overflow: hidden;
    background: var(--page-bg);
  }
  .billboard {
    position: absolute;
    left: 0;
    top: 200px;
    width: 1200px;
    height: 600px;
    background: var(--board-blue);
    font-family: "Patua One", "Bree Serif", serif;
    color: var(--text-white);
  }
  .brand-mark {
    position: absolute;
    left: 185px;
    top: 72px;
    width: 200px;
    height: 200px;
    border-radius: 50%;
    background: var(--brand-green);
  }
  .practice-name {
    position: absolute;
    left: 420px;
    top: 40px;
    width: 700px;
    text-align: center;
    line-height: 1;
    font-weight: 400;
  }
  .practice-name .name-main {
    display: block;
    font-size: 104px;
  }
  .practice-name .name-sub {
    display: block;
    font-size: 74px;
    margin-top: 14px;
  }
  .name-rule {
    position: absolute;
    left: 427px;
    top: 261px;
    width: 628px;
    height: 2px;
    background: linear-gradient(90deg, rgba(255,255,255,0), #ffffff 20%, #ffffff 80%, rgba(255,255,255,0));
  }
  .website {
    position: absolute;
    left: 427px;
    top: 270px;
    width: 628px;
    text-align: center;
    font-family: "Bree Serif", serif;
    font-size: 29px;
    line-height: 1.2;
    color: var(--brand-green);
  }
  .services-frame {
    position: absolute;
    left: 0;
    top: 0;
  }
  .services-title {
    position: absolute;
    left: 497px;
    top: 320px;
    width: 200px;
    text-align: center;
    font-family: "Bree Serif", serif;
    font-weight: 400;
    font-size: 29px;
    line-height: 1.2;
    color: var(--brand-green);
  }
  .services-list {
    position: absolute;
    left: 0;
    top: 0;
    list-style: none;
    font-family: "Bree Serif", serif;
    font-size: 25px;
  }
  .services-list li {
    position: absolute;
    display: flex;
    align-items: center;
    gap: 6px;
    white-space: nowrap;
  }
  .services-list svg { width: 14px; height: 16px; flex: none; }
  .call-line {
    position: absolute;
    left: 0;
    top: 482px;
    width: 1200px;
    text-align: center;
    font-size: 74px;
    line-height: 1;
    letter-spacing: 1px;
  }
  .call-line .call-label { color: var(--brand-green); margin-right: 16px; }
  .call-line .call-phone { color: var(--text-white); }
</style>
</head>
<body>
  <main class="billboard">
    <div class="brand-mark" aria-hidden="true"></div>

    <h1 class="practice-name">
      <span class="name-main">Harlow Brook</span>
      <span class="name-sub">Dentistry</span>
    </h1>
    <div class="name-rule"></div>
    <p class="website">Harlowbrookdentistry.example</p>

    <svg class="services-frame" width="1200" height="600" aria-hidden="true">
      <polyline points="490,339 47,339 47,432 64,432" fill="none" stroke="#ffffff" stroke-width="3"/>
      <polyline points="704,339 1153,339 1153,432 1136,432" fill="none" stroke="#ffffff" stroke-width="3"/>
    </svg>
    <h2 class="services-title">Our Services</h2>

    <ul class="services-list">
      <li style="left:89px;top:360px"><svg viewBox="0 0 14 16"><path d="M2 8l4 4 6-10" fill="none" stroke="#6bb83f" stroke-width="2.5"/></svg>Crowns</li>
      <li style="left:89px;top:396px"><svg viewBox="0 0 14 16"><path d="M2 8l4 4 6-10" fill="none" stroke="#6bb83f" stroke-width="2.5"/></svg>Root Canals</li>
      <li style="left:89px;top:432px"><svg viewBox="0 0 14 16"><path d="M2 8l4 4 6-10" fill="none" stroke="#6bb83f" stroke-width="2.5"/></svg>Extractions</li>
      <li style="left:368px;top:360px"><svg viewBox="0 0 14 16"><path d="M2 8l4 4 6-10" fill="none" stroke="#6bb83f" stroke-width="2.5"/></svg>Implants</li>
      <li style="left:368px;top:396px"><svg viewBox="0 0 14 16"><path d="M2 8l4 4 6-10" fill="none" stroke="#6bb83f" stroke-width="2.5"/></svg>Bridges</li>
      <li style="left:368px;top:432px"><svg viewBox="0 0 14 16"><path d="M2 8l4 4 6-10" fill="none" stroke="#6bb83f" stroke-width="2.5"/></svg>Clear Aligner</li>
      <li style="left:655px;top:360px"><svg viewBox="0 0 14 16"><path d="M2 8l4 4 6-10" fill="none" stroke="#6bb83f" stroke-width="2.5"/></svg>Veneers</li>
      <li style="left:655px;top:396px"><svg viewBox="0 0 14 16"><path d="M2 8l4 4 6-10" fill="none" stroke="#6bb83f" stroke-width="2.5"/></svg>Whitening</li>
      <li style="left:655px;top:432px"><svg viewBox="0 0 14 16"><path d="M2 8l4 4 6-10" fill="none" stroke="#6bb83f" stroke-width="2.5"/></svg>Fillings</li>
      <li style="left:910px;top:360px"><svg viewBox="0 0 14 16"><path d="M2 8l4 4 6-10" fill="none" stroke="#6bb83f" stroke-width="2.5"/></svg>Cleanings</li>
      <li style="left:910px;top:396px"><svg viewBox="0 0 14 16"><path d="M2 8l4 4 6-10" fill="none" stroke="#6bb83f" stroke-width="2.5"/></svg>Dentures</li>
      <li style="left:910px;top:432px"><svg viewBox="0 0 14 16"><path d="M2 8l4 4 6-10" fill="none" stroke="#6bb83f" stroke-width="2.5"/></svg>Overdentures</li>
    </ul>

    <p class="call-line"><span class="call-label">CALL TODAY!</span><span class="call-phone">(555) 847-1390</span></p>
  </main>
</body>
</html>
```